Business Cards + Flyer + Letterhead for Care Recruitment Agency

We are a recruitment agency for the health & care sector. We need designs made for business cards, A5 double-sided flyer, and a letterhead template.

Our branding message is professionalism, care, compassion, expertise. We are experts in recruitment for the care & health industry.

Our logo source files and colours are here - https://www.filevault-example.net/sh/q8rn27lpzw4xkc/BBRtLm3QPW92dKfYhNvZceLmo?dl=0

For the business card, I have attached an example we like. We want a vertical business card design, something very similar to the example given. The design should match our logo in terms of brand colors. On one side should be our logo, our website (www.holbrookelune.co.uk) and Care Recruitment Specialists written somewhere visible that fits, between our logo and the website at the bottom. On the other side should be our details.

Details on the front:

Logo with slogan
Care Recruitment Specialists
www.holbrookelune.co.uk

Details on the back:

Dominic Argyros
Managing Director

Radley Court, 40-48 Pellow St, Birmingham, B7 9QX
07612 495137
dominic@holbrookelune.co.uk
www.holbrookelune.co.uk

Nadia Holbrooke
Business Development Director

07731 284956
nadia@holbrookelune.co.uk
www.holbrookelune.co.uk

For the A5 flyer, I have attached some pictures we've used for the website, which could be used for the flyer as well. To get a better idea of our branding, please visit our website - https://holbrookelune.co.uk/

The text for the flyer is also attached.

Finally, the letterhead template should be a docx template with our logo and our identifiable branding (the same shapes and matching colours you will come up with for the business cards and flyer).

```html
<!DOCTYPE html>
<html lang="en">
<head>
<meta charset="utf-8">
<title>Holbrooke Lune – Letterhead and Business Cards</title>
<link href="https://fonts.googleapis.com/css2?family=Montserrat:wght@500;600&family=Open+Sans:wght@400;600&family=Arimo:wght@400;700&display=swap" rel="stylesheet">
<style>
  :root{
    --canvas:#e9ebee;
    --paper:#ffffff;
    --navy:#0c1c48;
    --brand-navy:#0b2a6e;
    --blue:#0a6cf0;
    --cyan:#00c8f8;
    --accent:#1e8ff5;
    --ink:#4a4a4a;
    --ink-strong:#333333;
    --white:#ffffff;
  }
  *{box-sizing:border-box;margin:0;padding:0}
  html,body{width:1200px;height:1000px;overflow:hidden;background:var(--canvas)}
  .canvas{position:relative;width:1200px;height:1000px}

  /* Letterhead */
  .letterhead{position:absolute;left:100px;top:200px;width:464px;height:594px;background:var(--paper);
    box-shadow:0 2px 8px rgba(0,0,0,.12);overflow:hidden;font-family:"Open Sans",sans-serif;color:var(--ink)}
  .lh-brand{position:absolute;left:42px;top:14px;display:flex;align-items:center;gap:8px}
  .brand-dot{width:36px;height:36px;border-radius:50%;background:var(--accent)}
  .brand-name{font-family:"Montserrat",sans-serif;font-weight:600;color:var(--brand-navy);letter-spacing:1.5px;line-height:1}
  .brand-slogan{font-family:"Montserrat",sans-serif;font-weight:600;color:var(--brand-navy);letter-spacing:1.6px;line-height:1}
  .lh-brand .brand-name{font-size:14.5px}
  .lh-brand .brand-slogan{font-size:7.5px;margin-top:3px;padding-left:22px}
  .lh-tagline{position:absolute;left:60px;top:61px;font-size:8.6px;font-weight:600;color:var(--ink-strong);letter-spacing:.2px}
  .lh-body{position:absolute;left:44px;top:107px;width:375px;font-size:7.6px;line-height:13.4px}
  .lh-body p{margin-bottom:13.4px;text-align:justify}
  .lh-body .recipient{line-height:9px;margin-bottom:22px;text-align:left}
  .lh-body .date{margin-bottom:8px}
  .lh-closing{position:absolute;left:44px;top:401px;font-size:7.6px}
  .signature{display:block;margin-top:6px;width:106px;height:14px;background:linear-gradient(90deg,#e6e6e6,#f3f3f3);border-radius:3px}
  .signer-name{margin-top:6px;font-size:9.5px;color:var(--ink-strong)}
  .signer-role{margin-top:2px}
  .lh-bands{position:absolute;left:0;bottom:0;width:464px;height:109px}
  .lh-footer{position:absolute;left:47px;top:557px;font-size:8.8px;color:var(--white);line-height:14.5px}
  .lh-footer .address{display:inline-block;border-bottom:1px solid rgba(255,255,255,.7);line-height:12px}
  .lh-footer b{font-weight:600}

  /* Business cards */
  .card{position:absolute;top:361px;height:397px;background:var(--paper);overflow:hidden;
    box-shadow:0 2px 8px rgba(0,0,0,.14);font-family:"Arimo",sans-serif}
  .card-front{left:620px;width:246px}
  .card-back{left:886px;width:244px}
  .card-bands{position:absolute;inset:0;width:100%;height:100%}
  .front-brand{position:absolute;left:0;right:0;top:36px;text-align:center}
  .front-brand .brand-dot{width:70px;height:70px;margin:0 auto 20px}
  .front-brand .brand-name{font-size:19px;letter-spacing:2.2px}
  .front-brand .brand-slogan{font-size:9.5px;letter-spacing:2px;margin-top:4px}
  .front-tagline{position:absolute;left:0;right:0;top:350px;text-align:center;font-size:12.5px;color:var(--accent);letter-spacing:.3px}
  .holder{position:absolute;left:21px;top:76px}
  .holder-name{font-size:19px;font-weight:700;color:var(--brand-navy);letter-spacing:-.2px}
  .holder-role{font-size:12.5px;color:var(--accent);margin-top:3px}
  .contacts{position:absolute;left:21px;top:290px;list-style:none;color:var(--white);font-size:11.8px}
  .contacts li{display:flex;align-items:flex-start;gap:4px;line-height:14.5px}
  .contacts li.address{margin-top:7px}
  .contacts svg{flex:none;width:13px;height:13px;margin-top:1px}
</style>
</head>
<body>
<div class="canvas">

  <section class="letterhead">
    <div class="lh-brand">
      <span class="brand-dot"></span>
      <div>
        <div class="brand-name">HOLBROOKE LUNE</div>
        <div class="brand-slogan">CARING IS OUR CALLING</div>
      </div>
    </div>
    <div class="lh-tagline">CARE RECRUITMENT SPECIALISTS</div>

    <div class="lh-body">
      <p class="date">Issuing Date: May 5, 2018</p>
      <p class="recipient">Name Of Employee Mr. XYZABC<br>Address of Employee<br>Address Line 2 etc..</p>
      <p>Dear Mr.XYZABC</p>
      <p>Lorem Ipsum has been the industry's standard dummy text ever since the 1500s, when an unknown printer took a galley of type and scrambled it to make a type specimen book. It has survived not only five centuries, but also the leap into electronic typesetting, remaining essentially unchanged. It was popularised in the 1960s with the release of Typeline sheets containing Lorem Ipsum passages, and more recently with desktop publishing software like Pagewright Studio including versions of Lorem Ipsum.</p>
      <p>Lorem Ipsum is simply dummy text of the printing and typesetting industry. Lorem Ipsum has been the industry's standard dummy text ever since the 1500s, when an unknown printer took a galley of type and scrambled it to make a type specimen book.</p>
      <p>It has survived not only five centuries, but also the leap into electronic typesetting, remaining essentially unchanged. It was popularised in the 1960s with the release of Typeline sheets containing Lorem Ipsum passages.</p>
    </div>

    <div class="lh-closing">
      <div>Yours Sincerely</div>
      <span class="signature" role="img" aria-label="Handwritten signature of Marcus Ellery"></span>
      <div class="signer-name">Marcus Ellery</div>
      <div class="signer-role">Managing Director</div>
    </div>

    <svg class="lh-bands" viewBox="0 0 464 109" aria-hidden="true">
      <path fill="var(--cyan)" d="M0 49 C160 44 320 30 464 0 V109 H0Z"/>
      <path fill="var(--blue)" d="M0 54 C160 49 320 38 464 9 V109 H0Z"/>
      <path fill="var(--navy)" d="M0 60 C160 56 320 46 464 20 V109 H0Z"/>
    </svg>
    <div class="lh-footer">
      <span class="address">Radley Court, 40-48 Pellow St Birmingham, B7 9QX</span><br>
      <b>P:</b> 07612 495137 | <b>E:</b> dominic@holbrookelune.co.uk | www.holbrookelune.co.uk
    </div>
  </section>

  <section class="card card-front">
    <svg class="card-bands" viewBox="0 0 246 397" aria-hidden="true">
      <path fill="var(--cyan)" d="M0 262 C90 258 170 240 246 205 V397 H0Z"/>
      <path fill="var(--blue)" d="M0 270 C90 266 170 250 246 218 V397 H0Z"/>
      <path fill="var(--navy)" d="M0 282 C90 279 170 264 246 234 V397 H0Z"/>
    </svg>
    <div class="front-brand">
      <div class="brand-dot"></div>
      <div class="brand-name">HOLBROOKE LUNE</div>
      <div class="brand-slogan">CARING IS OUR CALLING</div>
    </div>
    <div class="front-tagline">CARE RECRUITMENT SPECIALISTS</div>
  </section>

  <section class="card card-back">
    <svg class="card-bands" viewBox="0 0 244 397" aria-hidden="true">
      <path fill="var(--cyan)" d="M0 212 C90 208 170 190 244 155 V397 H0Z"/>
      <path fill="var(--blue)" d="M0 220 C90 216 170 200 244 168 V397 H0Z"/>
      <path fill="var(--navy)" d="M0 232 C90 229 170 214 244 184 V397 H0Z"/>
    </svg>
    <div class="holder">
      <div class="holder-name">DOMINIC ARGYROS</div>
      <div class="holder-role">MANAGING DIRECTOR</div>
    </div>
    <ul class="contacts">
      <li>
        <svg viewBox="0 0 14 14" aria-hidden="true"><circle cx="7" cy="7" r="6" fill="none" stroke="var(--accent)" stroke-width="1.2"/><path d="M5 4 L6 4 L6.6 5.6 L5.9 6.2 C6.3 7 7 7.7 7.8 8.1 L8.4 7.4 L10 8 L10 9 C7 9.5 4.5 7 5 4Z" fill="var(--accent)"/></svg>
        07612 495137
      </li>
      <li>
        <svg viewBox="0 0 14 14" aria-hidden="true"><circle cx="7" cy="7" r="6" fill="none" stroke="var(--accent)" stroke-width="1.2"/><circle cx="7" cy="7" r="3.3" fill="none" stroke="var(--accent)" stroke-width="1"/><path d="M3.7 7 H10.3 M7 3.7 V10.3" stroke="var(--accent)" stroke-width=".8"/></svg>
        www.holbrookelune.co.uk
      </li>
      <li>
        <svg viewBox="0 0 14 14" aria-hidden="true"><circle cx="7" cy="7" r="6" fill="none" stroke="var(--accent)" stroke-width="1.2"/><rect x="4" y="5" width="6" height="4.2" fill="var(--accent)"/><path d="M4 5 L7 7.3 L10 5" fill="none" stroke="var(--navy)" stroke-width=".7"/></svg>
        dominic@holbrookelune.co.uk
      </li>
      <li class="address">
        <svg viewBox="0 0 14 14" aria-hidden="true"><circle cx="7" cy="7" r="6" fill="none" stroke="var(--accent)" stroke-width="1.2"/><path d="M7 10.5 C5 8.2 4.6 7.2 4.6 6 A2.4 2.4 0 0 1 9.4 6 C9.4 7.2 9 8.2 7 10.5Z" fill="none" stroke="var(--accent)" stroke-width="1"/><circle cx="7" cy="6" r=".9" fill="var(--accent)"/></svg>
        <span>Radley Court, 40-48 Pellow St<br>Birmingham, B7 9QX</span>
      </li>
    </ul>
  </section>

</div>
</body>
</html>
```